Zenqo - revolutionary mobile payment

The app is a P2P money trasfert, without the using of credit card or bank circuits it can transfer electronic money from one person to another consumers simply and immediatelly.
You can use the color you want, but the message we need to transert to consumer is simplicity, safety and coolness.
In attach the logo of the company and the wireframe of thre page of the app.
The goal is to design the page of the app with a clear, simple and intuitive graphic.
Updates

I have upgrade the brief with important information and detail, many thanks

Target Market(s)

all the people

Industry/Entity Type

Credit Card

Requirements
Must have
• You have to design one icon for each button in the first page, (shop is: where to shop)
in the second one a new intuitive image (instead of the hand) that let the user to understand that with a simple swipe he can process the payment
Nice to have
• You can include or esxclude what you want or belive can improve user experience of the app
Should not have
• too much color, too much button or information

```html
<!DOCTYPE html>
<html lang="en">
<head>
<meta charset="utf-8">
<title>Zenqo – Home</title>
<link href="https://fonts.googleapis.com/css2?family=Roboto:wght@300;400&display=swap" rel="stylesheet">
<style>
  :root {
    --backdrop: #e6e8ec;
    --status-blue: #5470a8;
    --header-blue: #4f6ba3;
    --profile-bg: #eef0f4;
    --profile-text: #7a8191;
    --tile-navy: #1f3b7a;
    --tile-deep: #1b336c;
    --tile-light: #26448a;
    --tile-line: rgba(255,255,255,0.08);
    --white: #ffffff;
    --avatar-tone: #b98a74;
  }
  * { box-sizing: border-box; margin: 0; padding: 0; }
  html, body { width: 1200px; height: 751px; overflow: hidden; }
  body {
    background: var(--backdrop);
    font-family: "Roboto", "Helvetica Neue", Arial, sans-serif;
    position: relative;
  }
  .app-screen {
    position: absolute;
    left: 403px; top: 25px;
    width: 394px; height: 700px;
    background: var(--tile-navy);
    overflow: hidden;
    display: flex; flex-direction: column;
  }
  .status-bar {
    height: 24px; background: var(--status-blue);
    color: var(--white); font-size: 11px;
    display: flex; align-items: center; justify-content: space-between;
    padding: 0 8px;
  }
  .status-bar .signal { display: flex; gap: 2px; align-items: center; }
  .status-bar .dot { width: 5px; height: 5px; border-radius: 50%; background: var(--white); }
  .status-bar .dot.empty { background: transparent; border: 1px solid var(--white); }
  .status-bar .battery { display: flex; align-items: center; gap: 3px; }
  .battery-body { width: 22px; height: 9px; border: 1px solid var(--white); padding: 1px; }
  .battery-body span { display: block; width: 100%; height: 100%; background: var(--white); }
  .account-header {
    height: 36px; background: var(--header-blue);
    color: var(--white); font-size: 14px; font-weight: 300;
    display: flex; align-items: center; justify-content: space-between;
    padding: 0 10px;
  }
  .profile-row {
    height: 48px; background: var(--profile-bg);
    display: flex; align-items: center; gap: 14px; padding: 0 10px;
    color: var(--profile-text); font-size: 14px;
  }
  .avatar { width: 34px; height: 34px; border-radius: 50%; background: radial-gradient(circle at 50% 40%, var(--avatar-tone), #6b4a3e); }
  .action-grid {
    flex: 1; display: grid;
    grid-template-columns: 1fr 1fr; grid-template-rows: 1fr 1fr;
    background: linear-gradient(135deg, var(--tile-deep) 0%, var(--tile-navy) 50%, var(--tile-light) 100%);
  }
  .action-tile {
    display: flex; flex-direction: column; align-items: center; justify-content: center; gap: 10px;
    color: var(--white); font-size: 30px; font-weight: 300;
    border-right: 1px solid var(--tile-line); border-bottom: 1px solid var(--tile-line);
  }
  .action-tile.pay { background: linear-gradient(160deg, rgba(0,0,0,0.12) 40%, transparent 40%); }
  .action-tile svg { width: 72px; height: 52px; fill: none; stroke: var(--white); stroke-width: 2.4; stroke-linejoin: round; stroke-linecap: round; }
</style>
</head>
<body>
  <main class="app-screen">
    <div class="status-bar">
      <div class="signal">
        <span class="dot"></span><span class="dot"></span><span class="dot"></span><span class="dot empty"></span><span class="dot empty"></span>
      </div>
      <span class="time">4:39 PM</span>
      <div class="battery">100% <div class="battery-body"><span></span></div></div>
    </div>
    <header class="account-header">
      <span class="phone-number">+320455127809</span>
      <svg class="settings-icon" width="20" height="20" viewBox="0 0 20 20" aria-label="Settings">
        <circle cx="10" cy="10" r="6" fill="none" stroke="#fff" stroke-width="1.4" stroke-dasharray="3 1.7"/>
        <circle cx="10" cy="10" r="2.6" fill="none" stroke="#fff" stroke-width="1.4"/>
      </svg>
    </header>
    <div class="profile-row">
      <div class="avatar" role="img" aria-label="User profile photo"></div>
      <span class="plan-label">Basic</span>
    </div>
    <nav class="action-grid">
      <div class="action-tile pay">
        <svg viewBox="0 0 72 52"><rect x="10" y="4" width="58" height="34"/><rect x="4" y="12" width="58" height="34"/><circle cx="33" cy="29" r="11"/><text x="33" y="35" text-anchor="middle" font-size="17" fill="#fff" stroke="none" font-family="Roboto, sans-serif">$</text></svg>
        <span>Pay</span>
      </div>
      <div class="action-tile ask">
        <svg viewBox="0 0 72 52"><rect x="6" y="14" width="52" height="32"/><line x1="14" y1="28" x2="32" y2="28"/><line x1="14" y1="36" x2="40" y2="36"/><path d="M50 34 L62 6 L68 9 L56 37 L49 40 Z"/></svg>
        <span>Ask</span>
      </div>
      <div class="action-tile account">
        <svg viewBox="0 0 72 52"><rect x="4" y="4" width="64" height="44" rx="3"/><line x1="4" y1="13" x2="68" y2="13"/><rect x="28" y="28" width="16" height="13"/><path d="M31 28 v-5 a5 5 0 0 1 10 0 v5"/></svg>
        <span>Account</span>
      </div>
      <div class="action-tile shop">
        <svg viewBox="0 0 72 52"><path d="M2 8 h9 l7 26 h30 l6 -20 h-38"/><circle cx="22" cy="44" r="3.5"/><circle cx="44" cy="44" r="3.5"/><path d="M62 24 c-6 -7 -8 -10 -8 -14 a8 8 0 0 1 16 0 c0 4 -2 7 -8 14 z"/><circle cx="62" cy="10" r="2.5"/></svg>
        <span>Shop</span>
      </div>
    </nav>
  </main>
</body>
</html>
```